Website for Dental Office - The Bright Arch Clinic

The bright arch clinic is a dental office offering cosmetic dentistry, general dentistry, and multi-specialty dental care all under one roof in our state-of-the-art cosmetic dental center. We are particularly striving to provide services that fit the need of the young generation. Thus, we hope to have a modern, professional concise website that represents our spirit.

*Should be able to switch from English to Chinese

6 sections besides homepage:
Home, Meet us, Services,
Patient Info, Cases&Reviews, Blog, Contact

The Services sections should contain multiple subsections such as cleaning and prevention, cosmetic dentistry, implant dentistry, removable dentures, etc...
The Patient Info section is also intended to contain several subsections such as
New Patient offer, accepted Insurance, patient portal, helpful tips, etc...

Target Market(s)

young generation

Coding

Coded - Design and coding required

Number of Pages Required

5+ page

Font styles to use
Sans Serif

Colors
0592cd
33a6d7
85cae6
00a990
33b8a4
86cfc6
cee9f5
cfeae6
3277b5

Requirements
Must have
• *Should be able to switch from English to Chinese
Nice to have
• http://www.thebrightarchclinic.com/
• As a reference, the above link is the current website, but we would like to change the appearance and the content (our new logo's picture is attached)

```html
<!DOCTYPE html>
<html lang="en">
<head>
<meta charset="utf-8">
<title>The Bright Arch Clinic</title>
<link href="https://fonts.googleapis.com/css2?family=Lato:wght@400;700&family=Montserrat:wght@600;700&display=swap" rel="stylesheet">
<style>
:root{
  --blue:#0592cd;
  --blue-mid:#33a6d7;
  --blue-light:#85cae6;
  --blue-pale:#cee9f5;
  --teal:#00a990;
  --teal-mid:#33b8a4;
  --teal-light:#86cfc6;
  --navy:#3277b5;
  --ink:#2b2b2b;
  --text:#555;
  --grey-bg:#f5f5f5;
  --footer:#1c1c1c;
  --footer-bar:#0f0f0f;
}
*{margin:0;padding:0;box-sizing:border-box}
html,body{width:1200px;height:3906px;overflow:hidden;background:#fff}
body{position:relative;font-family:'Lato',sans-serif;color:var(--text)}
.abs{position:absolute}
h1,h2,h3,.btn{font-family:'Montserrat',sans-serif}
.btn{position:absolute;display:flex;align-items:center;justify-content:center;border-radius:30px;color:#fff;font-weight:700;font-size:17px;letter-spacing:.3px;background:linear-gradient(90deg,var(--teal),var(--blue));box-shadow:0 3px 8px rgba(0,0,0,.12)}
.photo{position:absolute}

/* header + hero */
.hero{position:absolute;left:0;top:0;width:1200px;height:645px;background:linear-gradient(90deg,#f4f6f7 0%,#eef1f2 35%,#d9dcdc 60%,#c9b8a8 75%,#eceeee 100%)}
.brand{position:absolute;left:77px;top:28px;display:flex;align-items:center;gap:12px}
.brand-mark{width:40px;height:40px;background:var(--blue-mid);border-radius:4px}
.brand-name{font-family:'Montserrat',sans-serif;font-weight:700;font-size:18px;line-height:20px;color:var(--blue-mid);width:170px}
.nav{position:absolute;top:40px;left:0;font-size:13px;color:#333;letter-spacing:.2px}
.nav a{position:absolute;white-space:nowrap;color:#333;text-decoration:none}
.nav a.active{color:var(--blue-mid)}
.nav a.active::before{content:"";position:absolute;left:0;top:-9px;width:16px;height:1px;background:#999}
.lang{position:absolute;left:1050px;top:30px;width:72px;height:35px;background:var(--teal);color:#fff;font-size:13px;display:flex;align-items:center;justify-content:center;gap:10px;border-radius:2px}
.hero h1{position:absolute;left:79px;top:250px;font-size:40px;line-height:48px;color:var(--blue);font-weight:700}

/* welcome */
.welcome-frame{position:absolute;left:152px;top:730px;width:896px;height:479px;border:2px solid #333}
.welcome-gap{position:absolute;left:140px;top:813px;width:930px;height:311px;background:#fff}
.welcome h2{position:absolute;left:673px;top:836px;font-size:38px;color:var(--ink);font-weight:700}
.welcome p{position:absolute;left:673px;top:904px;width:450px;font-size:14px;line-height:25px;color:#555}

/* services */
.services{position:absolute;left:0;top:1291px;width:1200px;height:625px;background:var(--grey-bg)}
.section-title{position:absolute;font-size:38px;font-weight:700;color:var(--ink)}
.svc-label{position:absolute;height:62px;width:323px;background:#fff;display:flex;align-items:center;justify-content:center;font-size:19px;color:#333;box-shadow:0 2px 6px rgba(0,0,0,.08)}

/* patient info */
.pi-text{position:absolute;left:79px;width:450px;font-size:14px;line-height:25px;color:var(--navy)}
.pi-card{position:absolute;top:2445px;width:240px;height:135px;background:#fff;box-shadow:0 2px 10px rgba(0,0,0,.08);padding:26px 18px}
.pi-card h3{font-family:'Lato',sans-serif;font-weight:400;font-size:19px;color:#333;margin-bottom:10px}
.pi-card p{font-size:14px;line-height:25px;color:var(--navy)}

/* testimonials */
.reviews{position:absolute;left:0;top:2678px;width:1200px;height:594px;background:var(--grey-bg)}
.card-back{position:absolute;left:256px;top:2840px;width:688px;height:259px;background:#fff}
.card-front{position:absolute;left:299px;top:2799px;width:602px;height:352px;background:#fff;box-shadow:0 2px 14px rgba(0,0,0,.06);text-align:center}
.card-front p.quote{position:absolute;left:60px;top:86px;width:482px;font-size:16px;line-height:27px;color:#333}
.card-front .name{position:absolute;left:0;top:226px;width:100%;font-size:15px;color:var(--blue)}
.card-front .role{position:absolute;left:0;top:265px;width:100%;font-size:13px;color:#777}
.avatar{position:absolute;left:552px;top:2752px;width:94px;height:94px;border-radius:50%;border:2px solid var(--teal-mid);background:linear-gradient(135deg,#d9c3b0,#8d6d57)}
.dot{position:absolute;top:3182px;width:10px;height:10px;border-radius:50%;background:#777}

/* newsletter */
.newsletter{position:absolute;left:0;top:3272px;width:1200px;height:323px;background:linear-gradient(180deg,var(--teal) 0%,var(--blue) 100%)}
.newsletter h2{position:absolute;left:504px;top:3342px;font-size:36px;color:#fff;font-weight:700}
.newsletter-sub{position:absolute;left:504px;top:3405px;font-size:15px;color:#fff}
.email-field{position:absolute;left:502px;top:3451px;width:546px;height:61px;border-radius:31px;background:rgba(0,60,90,.25);padding-left:32px;display:flex;align-items:center;color:#fff;font-size:14px}
.subscribe{position:absolute;left:913px;top:3455px;width:135px;height:53px;border-radius:27px;background:#fff;color:var(--blue);font-family:'Montserrat',sans-serif;font-weight:700;font-size:16px;display:flex;align-items:center;justify-content:center}

/* footer */
.footer{position:absolute;left:0;top:3595px;width:1200px;height:251px;background:var(--footer)}
.foot-link{position:absolute;font-size:13px;color:#fff}
.foot-brand{position:absolute;left:380px;top:3680px;width:440px;text-align:center}
.foot-brand .mark{display:block;width:60px;height:60px;margin:0 auto 16px;background:var(--blue-light);border-radius:6px}
.foot-brand .name{font-family:'Montserrat',sans-serif;font-weight:700;font-size:22px;color:var(--blue-mid)}
.copyright{position:absolute;left:0;top:3846px;width:1200px;height:60px;background:var(--footer-bar);color:#ddd;font-size:13px;display:flex;align-items:center;justify-content:center}
</style>
</head>
<body>

<header class="hero">
  <div class="photo" role="img" aria-label="Smiling young woman seated in a dental chair in a bright clinic" style="left:420px;top:60px;width:780px;height:585px;background:radial-gradient(ellipse at 60% 40%,#b48c72 0%,#cfc1b4 35%,rgba(230,232,232,0) 70%)"></div>
  <div class="brand"><span class="brand-mark"></span><span class="brand-name">THE BRIGHT ARCH CLINIC</span></div>
  <nav class="nav">
    <a class="active" style="left:379px">HOME</a>
    <a style="left:449px">MEET US</a>
    <a style="left:532px">SERVICES</a>
    <a style="left:622px">PATIENT INFO</a>
    <a style="left:742px">CASES &amp; REVIEWS</a>
    <a style="left:884px">BLOG</a>
    <a style="left:950px">CONTACT</a>
  </nav>
  <div class="lang">EN <svg width="14" height="9" viewBox="0 0 14 9"><path d="M1 1l6 6 6-6" stroke="#fff" stroke-width="2" fill="none"/></svg></div>
  <h1>“YOUR SMILE. OUR<br>PASSION.”</h1>
  <div class="btn" style="left:77px;top:378px;width:283px;height:52px">REQUEST APPOINTMENT</div>
</header>

<section class="welcome">
  <div class="welcome-frame"></div>
  <div class="welcome-gap"></div>
  <div class="photo" role="img" aria-label="Patient receiving a dental check-up" style="left:77px;top:813px;width:448px;height:311px;background:linear-gradient(135deg,#e7c4b0 0%,#c99b86 40%,#6f9ad6 75%,#3f71c2 100%);box-shadow:6px 6px 12px rgba(0,0,0,.15)"></div>
  <h2>Welcome Visitors!</h2>
  <p>Welcome to The Bright Arch Clinic where we specialize in General and Cosmetic Dentistry, Dental Implants, Periodontics (Gum Surgery), Endodontics (Root Canal Treatment) and Reconstructive Dentistry for patients in Boston, Brookline, Cambridge, Brighton, Allston...</p>
  <div class="btn" style="left:675px;top:1036px;width:197px;height:52px">KNOW MORE</div>
</section>

<section class="services">
  <h2 class="section-title" style="left:0;width:1200px;text-align:center;top:56px">Dental Services</h2>
</section>
<div class="photo" role="img" aria-label="Dentist cleaning a patient's teeth with braces" style="left:77px;top:1429px;width:323px;height:228px;background:linear-gradient(135deg,#6b5a4d,#d2a995 50%,#8e86d6)"></div>
<div class="photo" role="img" aria-label="Dentist performing a cosmetic procedure" style="left:438px;top:1429px;width:323px;height:228px;background:linear-gradient(135deg,#7aa0c9,#b7cde2 45%,#e2b94a)"></div>
<div class="photo" role="img" aria-label="Smiling patient with a tooth shade guide" style="left:799px;top:1429px;width:323px;height:228px;background:linear-gradient(135deg,#e9dfd8,#d8b8a4 45%,#5fc1d0)"></div>
<div class="svc-label" style="left:77px;top:1678px">Cleaning and prevention</div>
<div class="svc-label" style="left:438px;top:1678px">Cosmetic dentistry</div>
<div class="svc-label" style="left:799px;top:1678px">Implant dentistry</div>
<div class="btn" style="left:511px;top:1782px;width:178px;height:51px">VIEW ALL</div>

<section class="patient-info">
  <h2 class="section-title" style="left:79px;top:2058px">Patient Info</h2>
  <p class="pi-text" style="top:2120px">Lorem ipsum dolor sit amet, consectetur adipiscing elit, sed do eiusmod tempor incididunt ut labore et dolore magna aliqua. Ut enim ad minim veniam, quis nostrud exercitation ullamco laboris nisi ut aliquip ex ea commodo consequat.</p>
  <p class="pi-text" style="top:2240px">Duis aute irure dolor in reprehendrit in voluptate velit esse cillum dolore eu fugiat nulla pariatur. Excepteur sint occaecat cupidatat non proident, sunt in culpa qui officia deserunt mollit anim id est laborum.</p>
  <div class="photo" role="img" aria-label="Smiling woman in a dental chair" style="left:699px;top:2010px;width:501px;height:353px;background:linear-gradient(120deg,#2b3f78 0%,#7b5a48 35%,#d6ab95 60%,#e6ecef 100%);box-shadow:-4px 6px 12px rgba(0,0,0,.15)"></div>
  <div class="pi-card" style="left:77px"><h3>New Patient offer</h3><p>Lorem ipsum dolor sit amet, consectetur adipiscing elit, sed.</p></div>
  <div class="pi-card" style="left:346px"><h3>Accepted Insurance</h3><p>Lorem ipsum dolor sit amet, consectetur adipiscing elit, sed.</p></div>
  <div class="pi-card" style="left:615px"><h3>Patient portal</h3><p>Lorem ipsum dolor sit amet, consectetur adipiscing elit, sed.</p></div>
  <div class="pi-card" style="left:883px"><h3>Helpful tips</h3><p>Lorem ipsum dolor sit amet, consectetur adipiscing elit, sed.</p></div>
</section>

<section class="reviews"></section>
<div class="card-back"></div>
<div class="card-front">
  <p class="quote">Lorem ipsum dolor sit amet, consectetur adipiscing elit, sed do eiusmod tempor incididunt ut labore et dolore magna aliqua. Ut enim ad minim veniam, quis nostrud exercitation ullamco laboris nisi ut aliquip ex ea commodo consequat.</p>
  <div class="name">-NAME SURNAME</div>
  <div class="role">Lorem ipsum dolor sit amet.</div>
</div>
<div class="avatar" role="img" aria-label="Reviewer portrait"></div>
<span class="dot" style="left:574px;background:#111"></span>
<span class="dot" style="left:595px"></span>
<span class="dot" style="left:616px"></span>

<section class="newsletter">
</section>
<div class="photo" role="img" aria-label="Smiling dentist in a white coat holding a clipboard" style="left:159px;top:3258px;width:258px;height:337px;background:linear-gradient(180deg,#5a3b2c 0%,#d7ae97 25%,#f4f6f8 45%,#dfe6ea 100%);border-radius:110px 110px 0 0"></div>
<h2 class="newsletter abs" style="background:none;height:auto;width:auto;top:3342px;left:504px;font-size:36px;color:#fff">Newsletter</h2>
<p class="newsletter-sub">Subscribe to our newsletter to get latest updates and news.</p>
<div class="email-field">Enter your email</div>
<div class="subscribe">SUBSCRIBE</div>

<footer class="footer"></footer>
<span class="foot-link" style="left:79px;top:3654px">Home</span>
<span class="foot-link" style="left:79px;top:3691px">Services</span>
<span class="foot-link" style="left:79px;top:3728px">Patient Info</span>
<span class="foot-link" style="left:79px;top:3764px">Cases</span>
<span class="foot-link" style="right:79px;top:3654px">Reviews</span>
<span class="foot-link" style="right:79px;top:3691px">Blog Post</span>
<span class="foot-link" style="right:79px;top:3728px">Meet us</span>
<span class="foot-link" style="right:79px;top:3764px">Contact</span>
<div class="foot-brand"><span class="mark"></span><span class="name">THE BRIGHT ARCH CLINIC</span></div>
<div class="copyright">©THE BRIGHT ARCH CLINIC- 2019. All Rights Reserved.</div>

</body>
</html>
```